Australian Trucking Company Requires Professional Looking Stationary

We require a professional looking stationary design that incorporates our newly designed logo.

Our business, called "Brell Haulage Contracting", provides contracting work, transport and logistics to business in Western Australia particularly with links to the mining sector.

We are a small business looking to expand and our new logo and our new stationary will help develop our brand image in our market place.

Target Market(s)

Businesses and Corporation with links to the Mining Sector

Industry/Entity Type

Small Business

Requirements
Must have
• The letterhead must have the following details:
The new logo

Text saying: "Brell Holdings Pty Ltd (ACN 582 316 907) ATF The Brell Discretionary Trust T/AS"
"ABN 71 834 209 553"
Address "P.O Box 817 Wattlegrove WA, 6958"
Phone: 08 9352 7140
Email: brellhaul@mailbox-example.com.au

The text on the letterhead should be editable as the details are likely to change in the near future. Provision should be made for a website address all though one isn't available at the moment.

The styling, layout and font text is entirely up to the designer.

```html
<!DOCTYPE html>
<html lang="en">
<head>
<meta charset="utf-8">
<title>Brell Haulage Contracting – Business Cards</title>
<link href="https://fonts.googleapis.com/css2?family=PT+Sans:wght@400;700&display=swap" rel="stylesheet">
<style>
  :root {
    --page: #ecebea;
    --card: #ffffff;
    --red: #e31b23;
    --red-dark: #b3151b;
    --ink: #3a3a3a;
    --ink-soft: #555555;
    --mark: #8a8a8a;
  }
  * { box-sizing: border-box; margin: 0; padding: 0; }
  html, body { width: 1200px; height: 711px; overflow: hidden; }
  body {
    background: var(--page);
    font-family: "PT Sans", "Myriad Pro", Arial, sans-serif;
    color: var(--ink);
    position: relative;
  }
  .card {
    position: absolute;
    width: 445px;
    height: 254px;
    background: var(--card);
    border-radius: 18px;
    overflow: hidden;
    box-shadow: 0 2px 6px rgba(0,0,0,0.18);
  }
  .card--front-a { left: 101px; top: 60px; }
  .card--front-b { left: 657px; top: 60px; }
  .card--back { left: 316px; top: 384px; width: 448px; height: 256px; }

  .brand {
    position: absolute;
    left: 14px;
    top: 12px;
    display: flex;
    align-items: center;
    gap: 14px;
  }
  .brand__square {
    width: 74px;
    height: 62px;
    background: var(--mark);
  }
  .brand__name {
    color: var(--red-dark);
    font-weight: 700;
    font-size: 21px;
    line-height: 23px;
    text-transform: uppercase;
    letter-spacing: 0.5px;
  }
  .abn {
    position: absolute;
    right: 15px;
    top: 9px;
    font-size: 10.5px;
  }
  .holder {
    position: absolute;
    left: 17px;
    top: 98px;
    font-size: 13px;
  }
  .holder strong { color: var(--red); font-weight: 700; }

  .contacts {
    position: absolute;
    left: 17px;
    list-style: none;
    font-size: 11px;
    line-height: 17.5px;
  }
  .card--front-a .contacts { top: 124px; }
  .card--front-b .contacts { top: 97px; }
  .contacts li { display: flex; align-items: center; gap: 5px; }
  .icon { width: 9px; height: 9px; fill: var(--ink); flex: none; }

  .band {
    position: absolute;
    top: 182px;
    height: 34px;
    background: var(--red);
    color: #fff;
    display: flex;
    align-items: center;
  }
  .band--main { left: 0; width: 325px; }
  .band--tail { left: 405px; right: 0; }
  .card--front-a .band--main { padding-left: 17px; font-size: 11px; gap: 5px; }
  .card--front-a .band--main .icon { fill: #fff; }
  .card--front-b .band--main {
    background: linear-gradient(90deg, var(--red-dark) 0%, var(--red) 45%);
    justify-content: flex-end;
    padding-right: 38px;
    font-size: 17px;
    font-weight: 700;
  }
  .band small { font-size: 12px; font-weight: 400; margin-left: 3px; }

  .legal {
    position: absolute;
    left: 0; right: 0;
    top: 228px;
    text-align: center;
    font-size: 10.5px;
  }

  .back-brand {
    position: absolute;
    left: 0; right: 0;
    top: 70px;
    display: flex;
    flex-direction: column;
    align-items: center;
    gap: 12px;
  }
  .back-brand .brand__square { width: 90px; height: 76px; }
  .back-brand .brand__name { color: var(--mark); font-size: 24px; line-height: 26px; text-align: center; }
  .back-web {
    position: absolute;
    left: 0; right: 0;
    top: 214px;
    text-align: center;
    font-size: 19px;
    color: var(--ink-soft);
    letter-spacing: 0.5px;
  }
</style>
</head>
<body>

<svg width="0" height="0" style="position:absolute" aria-hidden="true">
  <symbol id="i-home" viewBox="0 0 10 10"><path d="M5 0.5 0 5h1.5v4.5h2.7V6.5h1.6v3h2.7V5H10z"/></symbol>
  <symbol id="i-phone" viewBox="0 0 10 10"><path d="M2.2 0.6 3.8 2.4 2.9 3.6c.6 1.4 1.9 2.7 3.4 3.4l1.1-.9 1.9 1.6-.9 1.5C4.8 9.2.8 5.2.7 1.6z"/></symbol>
  <symbol id="i-mail" viewBox="0 0 10 10"><path d="M0.5 2h9v6.2h-9zM1 2.6 5 5.6 9 2.6v-.3H1z" fill-rule="evenodd"/></symbol>
  <symbol id="i-web" viewBox="0 0 10 10"><path d="M5 .4a4.6 4.6 0 1 0 0 9.2A4.6 4.6 0 0 0 5 .4zm0 1c.5.5 1 1.5 1.1 3.1H3.9C4 2.9 4.5 1.9 5 1.4zM1.4 5.5h1.5c.1 1.1.3 2 .7 2.7A3.6 3.6 0 0 1 1.4 5.5zm0-1a3.6 3.6 0 0 1 2.2-2.7c-.4.7-.6 1.6-.7 2.7zm3.6 4.1c-.5-.5-1-1.5-1.1-3.1h2.2C6 7.1 5.5 8.1 5 8.6zm1.4-.4c.4-.7.6-1.6.7-2.7h1.5a3.6 3.6 0 0 1-2.2 2.7zm.7-3.7C7 3.4 6.8 2.5 6.4 1.8a3.6 3.6 0 0 1 2.2 2.7z"/></symbol>
</svg>

<!-- Front, variant A -->
<section class="card card--front-a">
  <div class="brand">
    <span class="brand__square"></span>
    <span class="brand__name">Brell<br>Haulage<br>Contracting</span>
  </div>
  <p class="abn">ABN 71 834 209 553</p>
  <p class="holder"><strong>Your Name,</strong> Title</p>
  <ul class="contacts">
    <li><svg class="icon"><use href="#i-phone"/></svg>08 9352 7140</li>
    <li><svg class="icon"><use href="#i-mail"/></svg>brellhaul@mailbox-example.com.au</li>
    <li><svg class="icon"><use href="#i-web"/></svg>www.brellhaul-example.com</li>
  </ul>
  <div class="band band--main"><svg class="icon"><use href="#i-home"/></svg>P.O Box 817 Wattlegrove WA, 6958</div>
  <div class="band band--tail"></div>
  <p class="legal">Brell Holdings Pty Ltd (ACN 582 316 907) ATF The Brell Discretionary Trust T/AS</p>
</section>

<!-- Front, variant B -->
<section class="card card--front-b">
  <div class="brand">
    <span class="brand__square"></span>
    <span class="brand__name">Brell<br>Haulage<br>Contracting</span>
  </div>
  <p class="abn">ABN 71 834 209 553</p>
  <ul class="contacts">
    <li><svg class="icon"><use href="#i-home"/></svg>P.O Box 817 Wattlegrove WA, 6958</li>
    <li><svg class="icon"><use href="#i-phone"/></svg>08 9352 7140</li>
    <li><svg class="icon"><use href="#i-mail"/></svg>brellhaul@mailbox-example.com.au</li>
    <li><svg class="icon"><use href="#i-web"/></svg>www.brellhaul-example.com</li>
  </ul>
  <div class="band band--main">Your Name,<small>Title</small></div>
  <div class="band band--tail"></div>
  <p class="legal">Brell Holdings Pty Ltd (ACN 582 316 907) ATF The Brell Discretionary Trust T/AS</p>
</section>

<!-- Back -->
<section class="card card--back">
  <div class="back-brand">
    <span class="brand__square"></span>
    <span class="brand__name">Brell Haulage Contracting</span>
  </div>
  <p class="back-web">www.brellhaul-example.com</p>
</section>

</body>
</html>
```